New Innovative Counselling and psychotherapy Service needs Business Card design

Keep it simple and professional. On one side, just company name and logo (perhaps in all blue) and maybe a tag line.

On other side (all white) my name and Qualifications in centre

Industry/Entity Type

Health And Wellness

Contact Information for Business Card

Dara Whelby
Counsellor & Psychotherapist
BSc (Psychol.), BA, Dip. (Couns. & Psych.), PG.Cert (CBT), FGTrK, ONRE

I will also require Mobile no, Email and web site address of which I'll pass on to final designer.

Font styles to use
Sans Serif

Requirements
Must have
• My Logo Only and please use the colours in logo that is in it.
Should not have
• Any other images

```html
<!DOCTYPE html>
<html lang="en">
<head>
<meta charset="utf-8">
<title>Tendwell Path – Business Card</title>
<link href="https://fonts.googleapis.com/css2?family=Work+Sans:wght@300;400;500&display=swap" rel="stylesheet">
<style>
  :root {
    --backdrop: #262626;
    --card-light: #ffffff;
    --card-dark: #333333;
    --brand-blue: #4fb1e3;
    --ink: #2e2e2e;
    --ink-soft: #3a3a3a;
    --white: #ffffff;
  }
  * { box-sizing: border-box; margin: 0; padding: 0; }
  html, body {
    width: 1200px; height: 930px; overflow: hidden;
    background: var(--backdrop);
    font-family: "Work Sans", Arial, sans-serif;
  }
  .card {
    position: absolute; top: 293px;
    width: 540px; height: 310px;
    overflow: hidden;
  }
  .card--front { left: 42px; background: var(--card-light); }
  .card--back { left: 612px; background: var(--card-dark); }

  .brand {
    position: absolute;
    display: flex; align-items: center; gap: 14px;
  }
  .brand__dot {
    width: 50px; height: 50px; border-radius: 50%;
    background: var(--brand-blue);
    flex: none;
  }
  .brand__name {
    font-size: 26px; font-weight: 300; letter-spacing: 0.3px;
    color: var(--ink);
    white-space: nowrap;
  }
  .card--front .brand { left: 28px; top: 32px; }
  .card--back .brand { left: 206px; top: 124px; }
  .card--back .brand__dot { width: 54px; height: 54px; }
  .card--back .brand__name { color: var(--white); }

  .accent-circle {
    position: absolute;
    width: 270px; height: 270px; border-radius: 50%;
    background: var(--brand-blue);
  }
  .card--front .accent-circle { left: 408px; top: 0; }
  .card--back .accent-circle { left: -138px; top: -2px; }

  .person {
    position: absolute; left: 29px; top: 120px;
    color: var(--ink-soft);
  }
  .person__name {
    font-size: 26px; font-weight: 400; color: var(--brand-blue);
    letter-spacing: 0.2px; line-height: 30px;
  }
  .person__role, .person__quals {
    font-size: 13.5px; line-height: 17px; letter-spacing: 0.3px;
  }

  .contact {
    position: absolute; left: 29px; top: 227px;
    list-style: none;
    font-size: 14px; color: var(--ink);
  }
  .contact li {
    display: flex; align-items: center; gap: 7px;
    height: 20px;
  }
  .contact svg { width: 9px; height: 9px; flex: none; }
  .contact .accent { color: var(--brand-blue); }
</style>
</head>
<body>

<section class="card card--front">
  <div class="brand">
    <span class="brand__dot"></span>
    <span class="brand__name">Tendwell Path</span>
  </div>

  <div class="accent-circle" role="img" aria-label="Large brand decoration"></div>

  <div class="person">
    <h1 class="person__name">DARA WHELBY</h1>
    <p class="person__role">Counsellor &amp; Psychotherapist</p>
    <p class="person__quals">BSc (Psychol.), BA, Dip.<br>(Couns. &amp; Psych.), PG.Cert (CBT), FGTrK, ONRE</p>
  </div>

  <ul class="contact">
    <li>
      <svg viewBox="0 0 10 10"><path d="M2 1 L4 1 L4.5 3 L3.3 3.8 Q4.3 6 6.2 6.8 L7 5.5 L9 6 L9 8 Q5 9 2.5 6 Q1 3.5 2 1Z" fill="var(--brand-blue)"/></svg>
      555-014-2290
    </li>
    <li>
      <svg viewBox="0 0 10 10"><rect x="0.7" y="2" width="8.6" height="6" fill="none" stroke="var(--brand-blue)" stroke-width="1"/><path d="M0.7 2 L5 5.5 L9.3 2" fill="none" stroke="var(--brand-blue)" stroke-width="1"/></svg>
      info@tendwellpath.com
    </li>
    <li>
      <svg viewBox="0 0 10 10"><circle cx="5" cy="5" r="4.2" fill="none" stroke="var(--brand-blue)" stroke-width="0.9"/><ellipse cx="5" cy="5" rx="1.8" ry="4.2" fill="none" stroke="var(--brand-blue)" stroke-width="0.8"/><path d="M0.8 5 H9.2" stroke="var(--brand-blue)" stroke-width="0.8"/></svg>
      <span>www.<span class="accent">tendwellpath</span>.com</span>
    </li>
  </ul>
</section>

<section class="card card--back">
  <div class="accent-circle" role="img" aria-label="Large brand decoration"></div>
  <div class="brand">
    <span class="brand__dot"></span>
    <span class="brand__name">Tendwell Path</span>
  </div>
</section>

</body>
</html>
```